The Linen Loft Co

We need a business card design for our wardrobe company.
Please visit our website www.gentlelinenlofts.com to get an idea of who we are.

```html
<!DOCTYPE html>
<html lang="en">
<head>
<meta charset="UTF-8">
<title>The Linen Loft Co — Business Card</title>
<link rel="stylesheet" href="https://fonts.googleapis.com/css2?family=Poppins:wght@400;500;600&display=swap">
<style>
  :root {
    --backdrop: #2a2a2a;
    --card-dark: #000000;
    --card-light: #ffffff;
    --ink-light: #ffffff;
    --ink-dark: #111111;
  }
  html, body {
    margin: 0;
    padding: 0;
    width: 1200px;
    height: 800px;
    overflow: hidden;
    background: var(--backdrop);
    font-family: "Poppins", sans-serif;
  }
  .card {
    position: absolute;
    left: 100px;
    top: 117px;
    width: 1000px;
    height: 565px;
    background: var(--card-light);
    overflow: hidden;
  }
  .card-shape {
    position: absolute;
    inset: 0;
  }
  .contact {
    position: absolute;
    left: 46px;
    top: 150px;
    color: var(--ink-light);
  }
  .contact-name {
    margin: 0;
    font-size: 37px;
    font-weight: 500;
    line-height: 1.1;
  }
  .contact-role {
    margin: 0 0 18px;
    font-size: 22px;
    font-weight: 500;
    line-height: 1.2;
  }
  .contact-address {
    margin: 0 0 14px;
    font-size: 22px;
    font-weight: 400;
    line-height: 1.33;
    font-style: normal;
  }
  .contact-lines {
    margin: 0;
    font-size: 22px;
    font-weight: 400;
    line-height: 1.33;
  }
  .brand {
    position: absolute;
    left: 538px;
    top: 244px;
    display: flex;
    align-items: center;
    gap: 81px;
    color: var(--ink-dark);
  }
  .brand-mark {
    width: 64px;
    height: 64px;
    background: var(--ink-dark);
  }
  .brand-name {
    margin: 0;
    font-size: 18px;
    font-weight: 500;
    letter-spacing: 0.2px;
    text-transform: uppercase;
  }
  .brand-tagline {
    margin: 6px 0 0;
    font-size: 16px;
    font-weight: 500;
  }
</style>
</head>
<body>
  <div class="card">
    <svg class="card-shape" width="1000" height="565" viewBox="0 0 1000 565" aria-hidden="true">
      <path d="M0,0 L544,0 Q386,282 544,565 L0,565 Z" fill="var(--card-dark)"/>
      <path d="M528,0 Q370,282 530,565" fill="none" stroke="var(--card-light)" stroke-width="2"/>
    </svg>

    <div class="contact">
      <h1 class="contact-name">Daniel Hartley</h1>
      <p class="contact-role">President</p>
      <address class="contact-address">Harbour Yard, 42 Mill Lane,<br>Bristol BS3 4QT</address>
      <p class="contact-lines">
        0117 496 0281<br>
        info@gentlelinenlofts.com<br>
        www.gentlelinenlofts.com
      </p>
    </div>

    <div class="brand">
      <div class="brand-mark" aria-hidden="true"></div>
      <div>
        <p class="brand-name">The Linen Loft Co</p>
        <p class="brand-tagline">Built to Fit Every Room</p>
      </div>
    </div>
  </div>
</body>
</html>
```